MBR - Stationery Design Project

We need stationery based on our logo.

Company info :
Cabinet Voisard & Associés
Société à responsabilité limitée au capital de 200.000 FCFP
RCS Papeete 27586K - Numéro tahiti K73962
Centre d’affaires OPALE - Rue Gaston Perrin
BP 61384 MAHU POTE - 98752 Papeete
Tahiti - Polynésie française
Tél : +689 40 73 16 48
Fax : +689 40 39 64 91

Industry/Entity Type

It Company

Font styles to use
Sans Serif

```html
<!DOCTYPE html>
<html lang="fr">
<head>
<meta charset="utf-8">
<title>MBR – Cartes de visite</title>
<link href="https://fonts.googleapis.com/css2?family=Jost:wght@300;400;500&display=swap" rel="stylesheet">
<style>
  :root {
    --backdrop: #e8e8ea;
    --paper: #ffffff;
    --navy: #1d3461;
    --slate: #869a9d;
    --slate-text: #9aa8ab;
  }
  * { margin: 0; padding: 0; box-sizing: border-box; }
  html, body {
    width: 1200px; height: 1000px; overflow: hidden;
    background: var(--backdrop);
    font-family: "Jost", "Futura", sans-serif;
  }
  .stage { position: relative; width: 1200px; height: 1000px; }
  .card {
    position: absolute;
    width: 540px; height: 320px;
    background: var(--paper);
    box-shadow: 0 2px 4px rgba(0,0,0,0.12);
    overflow: hidden;
  }
  .card--front { left: 110px; top: 110px; }
  .card--back { left: 550px; top: 560px; }

  .brand { position: absolute; color: var(--navy); }
  .brand__row { display: flex; align-items: center; gap: 10px; }
  .brand__square { width: 12px; height: 12px; background: var(--slate); }
  .brand__mark {
    font-weight: 400; font-size: 70px; line-height: 1; letter-spacing: 2px;
    color: var(--navy);
  }
  .brand__name { font-weight: 400; font-size: 15px; color: var(--navy); margin-top: 2px; }
  .brand__tagline { font-weight: 300; font-size: 8px; color: var(--slate-text); letter-spacing: 0.3px; }
  .card--front .brand { left: 150px; top: 104px; }

  .card--back .band { position: absolute; left: 0; top: 0; }
  .card--back .brand { left: 110px; top: 78px; }
  .card--back .brand__mark { font-size: 40px; }
  .card--back .brand__square { width: 8px; height: 8px; }
  .card--back .brand__name { font-size: 10px; }
  .card--back .brand__tagline { font-size: 6px; }

  .holder { position: absolute; left: 40px; bottom: 42px; }
  .holder__name { font-weight: 300; font-size: 24px; color: var(--navy); line-height: 1.1; }
  .holder__role { font-weight: 300; font-size: 15px; color: var(--slate-text); }

  .contact {
    position: absolute; right: 24px; bottom: 96px;
    font-weight: 400; font-size: 9.5px; line-height: 1.45; color: var(--navy);
  }
  .contact__label { color: var(--slate-text); }
</style>
</head>
<body>
<main class="stage">
  <section class="card card--front" aria-label="Recto de la carte">
    <div class="brand">
      <div class="brand__row">
        <span class="brand__mark">MBR</span>
        <span class="brand__square"></span>
      </div>
      <p class="brand__name">Cabinet Voisard &amp; Associés</p>
      <p class="brand__tagline">Expertise-comptable · Audit · Conseil</p>
    </div>
  </section>

  <section class="card card--back" aria-label="Verso de la carte">
    <svg class="band" width="540" height="320" viewBox="0 0 540 320" aria-hidden="true">
      <polygon points="250,0 540,0 540,10 480,70 210,70 250,0" fill="var(--slate)"/>
      <polygon points="0,115 0,115 70,70 70,140 0,140" fill="var(--navy)"/>
      <rect x="0" y="85" width="62" height="55" fill="var(--navy)"/>
    </svg>
    <div class="brand">
      <div class="brand__row">
        <span class="brand__mark">MBR</span>
        <span class="brand__square"></span>
      </div>
      <p class="brand__name">Cabinet Voisard &amp; Associés</p>
      <p class="brand__tagline">Expertise-comptable · Audit · Conseil</p>
    </div>

    <div class="holder">
      <p class="holder__name">Marc Lefèvre</p>
      <p class="holder__role">Managing Director</p>
    </div>

    <address class="contact" style="font-style:normal">
      Centre d’affaires OPALE - Rue Gaston Perrin BP 61384<br>
      MAHU POTE - 98752 Papeete, Tahiti.<br>
      <span class="contact__label">Tél. :</span> +689 40 73 16 48 | <span class="contact__label">Fax :</span> +689 40 39 64 91
    </address>
  </section>
</main>
</body>
</html>
```